Product Packaging design for Vaporizer Battery box

We are looking for product packaging for a new line of Vaporizer Batteries. These batteries are all sold in bundle packs, and each battery has its own cardboard box. For example, the bundle packs are simply bagged up packs of 2, 3, 5, 10, 25, etc.

There are 4 different kinds of batteries that we need the packaging designed for. I have attached templates of the packaging for your reference. I would like the packaging to be a similar theme across all the batteries to keep things consistent.

More details about the 4 batteries can be found on our website at:
http://www.tidemarkgoodsdepot.example/product-category/vape_batteries/
Password: tidevisit

Packing Requirements

The packaging should have our company logo somewhere on it. I have attached a few different variations/orientations of our logo for you to choose between.

The name of the battery
Tidemark Goods 1300mAh Variable Voltage Large Capacity Battery
Tidemark Goods 400mAh Slim Variable Voltage Battery
Tidemark Goods 280mAh Slim Automatic Buttonless Battery
Tidemark Goods 350mAh KOV Slim Battery

Company website www.TidemarkGoodsDepot.example

For the Tidemark Goods 350mAh KOV Slim Battery, have the product packaging color scheme be Black base with Gold wording/trim. This battery only comes in black and gold, so the packaging will match.

Make sure to use the proper packaging template for the batteries. There are only two templates and pretty much the only difference is the size. They both fold up to be a rectangle package.

Industry/Entity Type

Product

Colors

Designer to choose colors to be used in the design.

Requirements
Must have
• Packing Requirements
• The packaging should have our company logo somewhere on it. I have attached a few different variations/orientations of our logo for you to choose between.
• The name of the battery
• Tidemark Goods 1300mAh Variable Voltage Large Capacity Battery
• Tidemark Goods 400mAh Slim Variable Voltage Battery
• Tidemark Goods 280mAh Slim Automatic Buttonless Battery
• Tidemark Goods 350mAh KOV Slim Battery
• Company website www.TidemarkGoodsDepot.example
• For the Tidemark Goods 350mAh KOV Slim Battery, have the product packaging color scheme be Black base with Gold wording/trim. This battery only comes in black and gold, so the packaging will match.
• Make sure to use the proper packaging template for the batteries. There are only two templates and pretty much the only difference is the size. They both fold up to be a rectangle package.

```html
<!DOCTYPE html>
<html lang="en">
<head>
<meta charset="utf-8">
<title>Tidemark Goods – Personal Vape Pen Box</title>
<link rel="stylesheet" href="https://fonts.googleapis.com/css2?family=Cinzel:wght@700&family=Montserrat:wght@400;500&display=swap">
<style>
  :root {
    --stage-light: #f7a21a;
    --stage-dark: #ec6e18;
    --ink: #111111;
    --panel-black: #1c1c1c;
    --silver-light: #e4e4e4;
    --silver-mid: #c4c4c4;
    --silver-dark: #9a9a9a;
    --label-light: #d8d8d8;
  }
  html, body {
    margin: 0;
    padding: 0;
    overflow: hidden;
  }
  .canvas {
    position: relative;
    width: 1200px;
    height: 843px;
    overflow: hidden;
    background: radial-gradient(ellipse at 45% 45%, var(--stage-light) 0%, var(--stage-dark) 75%);
  }
  .box-layout {
    position: absolute;
    left: 0;
    top: 0;
  }
  .brand-word {
    font-family: "Cinzel", serif;
    font-weight: 700;
    fill: var(--ink);
  }
  .product-line {
    font-family: "Montserrat", sans-serif;
    font-weight: 400;
    fill: var(--label-light);
    letter-spacing: 1.5px;
  }
  .option-label {
    font-family: "Montserrat", sans-serif;
    font-weight: 500;
    font-size: 11px;
    fill: var(--ink);
    letter-spacing: 0.5px;
  }
  .option-box {
    fill: #ffffff;
    stroke: var(--ink);
    stroke-width: 1.2;
  }
  .signoff {
    position: absolute;
    right: 70px;
    bottom: 70px;
    display: flex;
    align-items: center;
    gap: 16px;
  }
  .signoff-mark {
    width: 60px;
    height: 60px;
    background: var(--ink);
  }
  .signoff-name {
    font-family: "Cinzel", serif;
    font-weight: 700;
    font-size: 44px;
    line-height: 1;
    color: var(--ink);
  }
</style>
</head>
<body>
<div class="canvas">
  <svg class="box-layout" width="1200" height="843" viewBox="0 0 1200 843" xmlns="http://www.w3.org/2000/svg">
    <defs>
      <linearGradient id="silverFace" x1="0" y1="0" x2="0" y2="1">
        <stop offset="0" stop-color="#efefef"/>
        <stop offset="0.5" stop-color="#cfcfcf"/>
        <stop offset="1" stop-color="#dcdcdc"/>
      </linearGradient>
      <linearGradient id="endCap" x1="0" y1="0" x2="1" y2="1">
        <stop offset="0" stop-color="#f4f4f4"/>
        <stop offset="0.5" stop-color="#b5b5b5"/>
        <stop offset="1" stop-color="#e6e6e6"/>
      </linearGradient>
    </defs>

    <g class="end-panel">
      <rect x="70" y="300" width="160" height="160" fill="url(#endCap)"/>
      <rect x="135" y="365" width="30" height="30" fill="var(--ink)"/>
    </g>

    <g class="front-panel">
      <rect x="240" y="300" width="890" height="160" fill="url(#silverFace)" role="img" aria-label="Grey interlocking geometric pattern printed on silver"/>
      <path class="band-left" d="M240 300 H390 C360 340 360 420 390 460 H240 Z" fill="var(--panel-black)"/>
      <path class="band-right" d="M800 300 H930 V460 H800 C830 420 830 340 800 300 Z" fill="var(--panel-black)"/>

      <text class="brand-word" x="592" y="394" font-size="38" text-anchor="middle">Tidemark Goods</text>

      <g class="product-name" transform="rotate(-90 868 380)">
        <text class="product-line" x="868" y="374" font-size="14" text-anchor="middle">PERSONAL</text>
        <text class="product-line" x="868" y="396" font-size="14" text-anchor="middle">VAPE PEN</text>
      </g>

      <g class="colour-options" transform="rotate(180 1030 380)">
        <g>
          <rect class="option-box" x="955" y="316" width="10" height="10"/><text class="option-label" x="971" y="325">SILVER</text>
          <rect class="option-box" x="955" y="341" width="10" height="10"/><text class="option-label" x="971" y="350">YELLOW</text>
          <rect class="option-box" x="955" y="366" width="10" height="10"/><text class="option-label" x="971" y="375">STAINLESS</text>
          <rect class="option-box" x="955" y="391" width="10" height="10"/><text class="option-label" x="971" y="400">PURPLE</text>
          <rect class="option-box" x="955" y="416" width="10" height="10"/><text class="option-label" x="971" y="425">GREEN</text>
        </g>
        <g>
          <rect class="option-box" x="1048" y="316" width="10" height="10"/><text class="option-label" x="1064" y="325">BLACK</text>
          <rect class="option-box" x="1048" y="341" width="10" height="10"/><text class="option-label" x="1064" y="350">BLUE</text>
          <rect class="option-box" x="1048" y="366" width="10" height="10"/><text class="option-label" x="1064" y="375">RED</text>
          <rect class="option-box" x="1048" y="391" width="10" height="10"/><text class="option-label" x="1064" y="400">WHITE</text>
          <rect class="option-box" x="1048" y="416" width="10" height="10"/><text class="option-label" x="1064" y="425">BLACK</text>
        </g>
      </g>
    </g>
  </svg>

  <div class="signoff">
    <div class="signoff-mark"></div>
    <div class="signoff-name">Tidemark Goods</div>
  </div>
</div>
</body>
</html>
```